RM Tomás Ledesma (Business Card)

Hi designers, in this work, I'm looking for an sophisticated stylish, elegant and proffesional personal card. We have a laboratory of pathology automated, with equipments high quality.
In this web the designers, have created my business logo, the name is "RM Tomás Ledesma"
In our lab, we principal work is to prepare the biopsies for further diagnostic of diseases like cancer, tumors, etc.
I need that the first face, only having my complete logo (Rm Tomás Ledesma, Laboratorio de procesamiento Histologico)
The overleaf, could repeat the same logo, like water logo.
In this face, I need to say: My full data:

Técnico en Anatomía Patológica
Tomás Ledesma Urquiza M.P 48213
Av. Duarte Quirós 817 - 2do piso - Instituto Brandsen.
Córdoba, Argentina
(0351) 158246093
ledesma.tomas@correoviva.com.ar

with respect the colors of card, use your imagination, the original logo color is violet, I haven't chosen a color base for the card.

attached pictures are examples of cards I like your DESIGN.
Attached too, the original logo to my company.

the size of card are:
horizontal: 9cm
vertical: 5,5cm

any question that you have, not doubt to question me,
Hand to work!

Industry/Entity Type

Laboratory

Requirements
Must have
• designers sophisticated, not simples, like show the images attached

```html
<!DOCTYPE html>
<html lang="es">
<head>
<meta charset="utf-8">
<title>RM Tomás Ledesma — Tarjeta personal</title>
<link rel="stylesheet" href="https://fonts.googleapis.com/css2?family=Roboto:wght@400;700&family=Roboto+Condensed:wght@300;400&display=swap">
<style>
  :root {
    --violet-light: #a14fd6;
    --violet: #8a34c6;
    --violet-deep: #5e1d9c;
    --paper: #ffffff;
    --paper-shade: #f2f2f3;
    --ink-grey: #7d7d83;
    --stage: #e9e6ec;
    --white: #ffffff;
  }
  * { box-sizing: border-box; margin: 0; padding: 0; }
  html, body {
    width: 1200px;
    height: 1023px;
    overflow: hidden;
    background: var(--stage);
  }
  .sheet {
    width: 1200px;
    height: 1023px;
    display: flex;
    flex-direction: column;
    align-items: center;
    justify-content: center;
    gap: 44px;
  }
  .card {
    position: relative;
    width: 740px;
    height: 452px;
    border-radius: 14px;
    overflow: hidden;
    box-shadow: 0 10px 28px rgba(60, 20, 90, 0.18);
  }
  .card--back {
    background: linear-gradient(200deg, var(--violet-light) 0%, var(--violet) 45%, var(--violet-deep) 100%);
  }

  /* Front */
  .card--front {
    background: linear-gradient(180deg, var(--paper) 0%, var(--paper-shade) 100%);
  }
  .brand {
    position: absolute;
    left: 0;
    top: 0;
    width: 290px;
    height: 100%;
    display: flex;
    flex-direction: column;
    align-items: center;
    justify-content: center;
    padding-top: 60px;
  }
  .brand__mark {
    display: flex;
    align-items: center;
    gap: 10px;
  }
  .brand__dot {
    width: 12px;
    height: 12px;
    border-radius: 50%;
    background: var(--violet);
  }
  .brand__name {
    font-family: "Roboto Condensed", "Arial Narrow", sans-serif;
    font-weight: 300;
    font-size: 19px;
    line-height: 24px;
    letter-spacing: 4px;
    text-transform: uppercase;
    color: var(--violet);
  }
  .brand__tagline {
    margin-top: 8px;
    font-family: "Roboto Condensed", "Arial Narrow", sans-serif;
    font-weight: 300;
    font-size: 12px;
    line-height: 16px;
    letter-spacing: 0.2px;
    text-transform: uppercase;
    color: var(--ink-grey);
    white-space: nowrap;
  }

  .details {
    position: absolute;
    left: 340px;
    top: 0;
    right: 0;
    bottom: 0;
    background: linear-gradient(200deg, var(--violet-light) 0%, var(--violet) 45%, var(--violet-deep) 100%);
    color: var(--white);
    font-family: "Roboto", Arial, sans-serif;
  }
  .details__name {
    position: absolute;
    left: 44px;
    top: 46px;
    font-weight: 700;
    font-size: 19px;
    line-height: 24px;
    white-space: nowrap;
  }
  .details__role {
    position: absolute;
    left: 44px;
    top: 72px;
    font-weight: 400;
    font-size: 13px;
    line-height: 16px;
    opacity: 0.9;
  }
  .contact {
    position: absolute;
    left: 44px;
    top: 143px;
    list-style: none;
  }
  .contact__item {
    font-size: 14px;
    line-height: 21px;
    margin-bottom: 26px;
    white-space: nowrap;
  }

  .markers {
    position: absolute;
    left: 0;
    top: 0;
    width: 740px;
    height: 452px;
    pointer-events: none;
  }
</style>
</head>
<body>
<main class="sheet">

  <section class="card card--front" aria-label="Frente de la tarjeta">
    <div class="brand">
      <div class="brand__mark">
        <span class="brand__dot"></span>
        <span class="brand__name">RM Tomás Ledesma</span>
      </div>
      <p class="brand__tagline">Laboratorio de procesamiento histológico</p>
    </div>

    <div class="details">
      <p class="details__name">Tomás Ledesma Urquiza M.P 48213</p>
      <p class="details__role">Técnico en Anatomía Patológica</p>
      <ul class="contact">
        <li class="contact__item">Av. Duarte Quirós 817 -<br>2do piso - Instituto Brandsen.<br>Córdoba, Argentina</li>
        <li class="contact__item">(0351) 158246093</li>
        <li class="contact__item">ledesma.tomas@correoviva.com.ar</li>
      </ul>
    </div>

    <svg class="markers" viewBox="0 0 740 452" aria-hidden="true">
      <polygon points="340,143.5 330,153.5 340,163.5" fill="#8a34c6"/>
      <polygon points="340,232.5 330,242.5 340,252.5" fill="#8a34c6"/>
      <polygon points="340,279.5 330,289.5 340,299.5" fill="#8a34c6"/>

      <g transform="translate(310 153.5)">
        <circle r="15" fill="#8a34c6"/>
        <path d="M0 -9 a6 6 0 0 1 6 6 c0 4.5 -6 11 -6 11 s-6 -6.5 -6 -11 a6 6 0 0 1 6 -6z" fill="#fff"/>
        <circle cy="-3" r="2.2" fill="#8a34c6"/>
      </g>

      <g transform="translate(310 242.5)">
        <circle r="15" fill="#8a34c6"/>
        <rect x="-5" y="-9" width="10" height="18" rx="2" fill="none" stroke="#fff" stroke-width="1.8"/>
        <line x1="-1.5" y1="5.5" x2="1.5" y2="5.5" stroke="#fff" stroke-width="1.6"/>
      </g>

      <g transform="translate(310 289.5)">
        <circle r="15" fill="#8a34c6"/>
        <rect x="-8" y="-6" width="16" height="12" rx="1.5" fill="#fff"/>
        <polyline points="-8,-5 0,1.5 8,-5" fill="none" stroke="#8a34c6" stroke-width="1.5"/>
      </g>
    </svg>
  </section>

  <section class="card card--back" aria-label="Dorso de la tarjeta"></section>

</main>
</body>
</html>
```